Card Design for my dog training business Brightpaw Obedience

Need a business card design for my dog training business with my new logo. Want the card to come off professional yet fun. Want it to be very eye catchy as well. I normally have these at vet clinics, pet stores, and groomers. so need it to look better than my competitors.
Target Market(s)
dog owners
Industry/Entity Type
Dog Training
Contact Information for Business Card
needs logo, my name and info
Font styles to use
Serif
Colors
0255a3
ffffff
ec1f27
000000
333333
fbfbfb
Requirements
Must have
- Brightpaw Obedience
- Felix Orland
- 415 903 2276
- info@brightpawobedience.example
- www.brightpawobedience.example

```html
<!DOCTYPE html>
<html lang="en">
<head>
<meta charset="utf-8">
<title>Brightpaw Obedience — Business Card</title>
<link rel="stylesheet" href="https://fonts.googleapis.com/css2?family=Libre+Baskerville:wght@400;700&display=swap">
<style>
  :root {
    --ink: #000000;
    --charcoal: #333333;
    --paper: #fbfbfb;
    --white: #ffffff;
    --signal-red: #ec1f27;
    --backdrop: #d9d9d9;
    --muted: #9a9a9a;
    --art-tone: #2a2a2a;
  }
  * { margin: 0; padding: 0; box-sizing: border-box; }
  html, body {
    width: 1200px; height: 900px; overflow: hidden;
    background: var(--backdrop);
    font-family: "Libre Baskerville", Georgia, serif;
  }
  .sheet {
    width: 1200px; height: 900px;
    display: flex; flex-direction: column;
    align-items: center; justify-content: center; gap: 40px;
  }
  .card {
    position: relative;
    width: 700px; height: 400px;
    background: var(--ink);
    overflow: hidden;
    box-shadow: 0 10px 30px rgba(0,0,0,.25);
  }

  /* Front */
  .identity { position: absolute; left: 48px; top: 58px; }
  .identity__name {
    font-size: 22px; letter-spacing: .04em; text-transform: uppercase;
    color: var(--white); font-weight: 400;
  }
  .identity__first { color: var(--signal-red); }
  .identity__role { margin-top: 8px; font-size: 14px; color: var(--muted); }
  .divider {
    position: absolute; left: 0; right: 40px; top: 138px;
    height: 1px; background: var(--signal-red);
  }
  .contacts {
    position: absolute; left: 48px; top: 168px;
    list-style: none; display: flex; flex-direction: column; gap: 14px;
  }
  .contacts__item {
    display: flex; align-items: center; gap: 14px;
    font-size: 15px; color: var(--muted);
  }
  .contacts__item:first-child { color: var(--white); }
  .contacts__icon { width: 20px; height: 20px; flex: none; }

  .brand {
    position: absolute; display: flex; align-items: center; gap: 12px;
    color: var(--white); font-size: 22px; font-weight: 400;
  }
  .brand__dot {
    width: 14px; height: 14px; border-radius: 50%;
    background: var(--white); flex: none;
  }
  .brand--front { right: 48px; bottom: 70px; }
  .brand--back { left: 48px; top: 52px; font-size: 20px; }

  /* Back */
  .backdrop-art {
    position: absolute; inset: 0;
    background:
      radial-gradient(ellipse 300px 210px at 62% 50%, var(--art-tone) 0%, rgba(42,42,42,.55) 45%, rgba(0,0,0,0) 100%),
      radial-gradient(ellipse 200px 150px at 80% 72%, rgba(42,42,42,.8) 0%, rgba(0,0,0,0) 100%),
      var(--ink);
  }
  .web-band {
    position: absolute; left: 200px; width: 390px; top: 160px; height: 40px;
    background: var(--signal-red);
    display: flex; align-items: center; padding-left: 24px;
    color: var(--white); font-size: 15px; letter-spacing: .12em;
    white-space: nowrap;
  }
</style>
</head>
<body>
<main class="sheet">

  <section class="card card--front" aria-label="Card front">
    <div class="identity">
      <h1 class="identity__name"><span class="identity__first">Felix</span> Orland</h1>
      <p class="identity__role">Owner</p>
    </div>
    <div class="divider"></div>
    <ul class="contacts">
      <li class="contacts__item">
        <svg class="contacts__icon" viewBox="0 0 20 20" aria-hidden="true">
          <circle cx="10" cy="10" r="10" fill="var(--signal-red)"/>
          <path d="M7 5.5c.6-.4 1.2 0 1.5.6l.7 1.4c.2.5 0 1-.4 1.2l-.6.4c.5 1.2 1.4 2.1 2.6 2.6l.4-.6c.3-.4.8-.6 1.2-.4l1.4.7c.6.3 1 .9.6 1.5-.6 1-1.7 1.4-2.8 1-2.6-.9-4.6-2.9-5.5-5.5-.4-1.1 0-2.2.9-2.9z" fill="var(--ink)"/>
        </svg>
        415 903 2276
      </li>
      <li class="contacts__item">
        <svg class="contacts__icon" viewBox="0 0 20 20" aria-hidden="true">
          <circle cx="10" cy="10" r="10" fill="var(--signal-red)"/>
          <rect x="5" y="6.5" width="10" height="7" fill="none" stroke="var(--ink)" stroke-width="1.3"/>
          <path d="M5 6.5l5 4 5-4" fill="none" stroke="var(--ink)" stroke-width="1.3"/>
        </svg>
        info@brightpawobedience.example
      </li>
      <li class="contacts__item">
        <svg class="contacts__icon" viewBox="0 0 20 20" aria-hidden="true">
          <circle cx="10" cy="10" r="10" fill="var(--signal-red)"/>
          <circle cx="10" cy="10" r="5" fill="none" stroke="var(--ink)" stroke-width="1.2"/>
          <path d="M5 10h10M10 5c-2 2.8-2 7.2 0 10M10 5c2 2.8 2 7.2 0 10" fill="none" stroke="var(--ink)" stroke-width="1.1"/>
        </svg>
        www.brightpawobedience.example
      </li>
    </ul>
    <div class="brand brand--front"><span class="brand__dot"></span>Brightpaw Obedience</div>
  </section>

  <section class="card card--back" aria-label="Card back">
    <div class="backdrop-art" role="img" aria-label="Large faint line illustration of two dogs over a state outline"></div>
    <div class="brand brand--back"><span class="brand__dot"></span>Brightpaw Obedience</div>
    <div class="web-band">www.brightpawobedience.example</div>
  </section>

</main>
</body>
</html>
```